Clear Harbor Business card

We are a company that owns 2 compliance software programs for TV, Radio and Cable industries as well as an online job board. We need a professional business card that incorproates all three logos.

```html
<!DOCTYPE html>
<html lang="en">
<head>
<meta charset="utf-8">
<title>Clear Harbor Business Card</title>
<link href="https://fonts.googleapis.com/css2?family=Lato:wght@400;700&family=Montserrat:wght@600;700&display=swap" rel="stylesheet">
<style>
  :root{
    --stage:#4b4b4b;
    --navy:#1c2f6b;
    --navy-deep:#172a5e;
    --orange:#e07740;
    --paper:#f1f1ef;
    --white:#ffffff;
  }
  *{margin:0;padding:0;box-sizing:border-box}
  html,body{width:1200px;height:829px;overflow:hidden}
  body{background:var(--stage);position:relative;font-family:'Lato',sans-serif}
  .card{position:absolute;top:282px;width:486px;height:277px;overflow:hidden;box-shadow:0 6px 14px rgba(0,0,0,.45)}
  .card-front{left:82px;background:linear-gradient(135deg,#233c8c 0%,var(--navy) 55%,var(--navy-deep) 100%);color:var(--white)}
  .card-back{left:628px;background:var(--paper)}
  .brand-row{position:absolute;left:50px;right:50px;display:flex;align-items:center;justify-content:center;gap:12px}
  .card-front .brand-row{top:118px}
  .card-back .brand-row{top:54px}
  .brand{display:flex;flex-direction:column;align-items:flex-start;line-height:1}
  .brand-name{font-family:'Montserrat',sans-serif;font-weight:700;font-size:13px;line-height:13px;white-space:nowrap}
  .brand-tag{font-family:'Montserrat',sans-serif;font-weight:600;font-size:5px;letter-spacing:.4px;margin-top:3px;text-transform:uppercase;white-space:nowrap}
  .brand-jobs{flex-direction:row;align-items:center;gap:6px}
  .brand-jobs .brand-text{display:flex;flex-direction:column}
  .brand-dot{width:18px;height:18px;border-radius:50%;background:currentColor;flex:none}
  .divider{width:1.5px;height:36px;background:currentColor;flex:none}
  .card-front .brand,.card-front .divider{color:var(--white)}
  .card-back .brand,.card-back .divider{color:var(--navy)}
  .front-url{position:absolute;bottom:32px;left:0;right:0;text-align:center;font-size:11px;letter-spacing:1.5px}
  .front-url b{font-weight:700}
  .band{position:absolute;top:142px;height:85px}
  .band-person{left:0;width:242px;background:var(--navy);color:var(--white);text-align:right;padding:13px 25px 0 0}
  .band-contact{left:244px;right:0;background:var(--orange);color:var(--white);padding:14px 0 0 25px}
  .person-name{font-weight:700;font-size:15px;margin-bottom:3px}
  .person-line{font-size:11.5px;line-height:15.5px}
  .contact-line{display:flex;align-items:center;gap:7px;font-size:11.5px;line-height:15.5px}
  .contact-line svg{width:9px;height:9px;flex:none}
</style>
</head>
<body>
  <section class="card card-front">
    <div class="brand-row">
      <div class="brand"><span class="brand-name">Clear Harbor</span><span class="brand-name">Broadcast</span><span class="brand-tag">Broadcast Compliance</span></div>
      <span class="divider"></span>
      <div class="brand"><span class="brand-name">Clear Harbor</span><span class="brand-name">Cable</span><span class="brand-tag">MVPD Compliance</span></div>
      <span class="divider"></span>
      <div class="brand brand-jobs"><span class="brand-dot"></span><span class="brand-text"><span class="brand-name">StageCall</span><span class="brand-name">Jobs</span></span></div>
    </div>
    <p class="front-url">www.<b>clearharbor</b>-co.com</p>
  </section>

  <section class="card card-back">
    <div class="brand-row">
      <div class="brand"><span class="brand-name">Clear Harbor</span><span class="brand-name">Broadcast</span><span class="brand-tag">Broadcast Compliance</span></div>
      <span class="divider"></span>
      <div class="brand"><span class="brand-name">Clear Harbor</span><span class="brand-name">Cable</span><span class="brand-tag">MVPD Compliance</span></div>
      <span class="divider"></span>
      <div class="brand brand-jobs"><span class="brand-dot"></span><span class="brand-text"><span class="brand-name">StageCall</span><span class="brand-name">Jobs</span></span></div>
    </div>
    <div class="band band-person">
      <p class="person-name">Daniel Mercer</p>
      <p class="person-line">Managing Director</p>
      <p class="person-line">Co. Street, Suite, Building</p>
      <p class="person-line">City/State, Zip Code</p>
    </div>
    <div class="band band-contact">
      <p class="contact-line"><svg viewBox="0 0 10 10"><path d="M2 1l2 2-1 1.2c.6 1.3 1.5 2.2 2.8 2.8L7 6l2 2-1.3 1.3C4.5 9 1 5.5.7 2.3Z" fill="#fff"/></svg>(555) 201-0140</p>
      <p class="contact-line"><svg viewBox="0 0 10 10"><rect x="1" y="4" width="8" height="5" rx="1" fill="#fff"/><path d="M0 3.5C2 1 8 1 10 3.5L8.5 4.5 7 3.5H3L1.5 4.5Z" fill="#fff"/></svg>(555) 201-0141</p>
      <p class="contact-line"><svg viewBox="0 0 10 10"><rect x=".8" y="2" width="8.4" height="6" fill="none" stroke="#fff"/><path d="M1 2.3 5 5.5 9 2.3" fill="none" stroke="#fff"/></svg>service@clearharbor-co.com</p>
      <p class="contact-line"><svg viewBox="0 0 10 10"><circle cx="5" cy="5" r="4" fill="none" stroke="#fff"/><path d="M1 5h8M5 1c-2 2.5-2 5.5 0 8M5 1c2 2.5 2 5.5 0 8" fill="none" stroke="#fff" stroke-width=".7"/></svg>www.clearharbor-co.com</p>
    </div>
  </section>
</body>
</html>
```